Shipping and Logistics, Project

Project description : Company Profile

A total logistics company covering domestic / international freight forwarding, warehouse management services, haulage, supply chain management, transport management & distribution, procurement & assembly services, shipping, chartering & bunker services, project logistics & tax exemption consultancy, oil & gas logistics, halal logistics services & integrated logistics management. We’re a well-established and experienced freight forwarder in Kuala Lumpur, Malaysia. We specialize in customized value-added solution that optimizes your supply chain by trimming inventory, reducing logistics cost and enhancing your customer service levels.

As a member of the Worldwide Parcel and Carriage Alliance which comprise of 170 global freight agents in 80 countries that promotes great handling in cross-trade logistics and freighting. You could rely on our efficiency in handlings of export cargo (FCL, LCL, Bulk and Conventional) between our global network offices worldwide with a total scale of 10,000 groomed specialists in various logistics division working together to ensure delivery task meets with your expectation. With our dedicated qualified and experienced professionals, we are fully committed to serving our clients.

Our generic services are listed below for your reference:

• Air Freight
• Ocean Freight FCL & LCL
• Container Haulage
• Warehousing
• Transportation and Distribution within Malaysia and Thailand
• Cross-Border Road Line-hauls between Thailand, Malaysia, Singapore and Laos
• Customs Brokerage and Forwarding
• Project Cargo Freight Forwarding for setting up of new plants / factories and ad hoc heavy-lift
• Air-Sea-Road-Rail multi-modal options
• Import / Export / Storage / Documentation / Handling of DG / Hazmat
• Vessel and Aircraft Charters

Our Mission
Based on the motto “Quick, Reliable and Polite”, we are dedicated to upholding the following three points corporate philosophy:
1. Adhering to the principle that “the customer always comes first”.
2. Contributing to the development of the local community.
3. Making it our duty to be responsible and sincere.

Our Edge
• One-Stop Logistics Solutions
• Extensive Network Throughout Malaysia
• Highly Qualified and Experienced Pool of Professionals
• Comprehensive IT Solutions
• Innovative and Customer-focused Solutions
• Flexible and Consistent in Managing Exceptions
• Total Supply Chain Visibility

Target Market
1. We sell the logistics services to all the industry in Malaysia and Worldwide. (ONE Stop Logistics Solutions)

Competitor
1. TR Valmont
2. Corvessa Transport
3. Brandt + Loewe
4. FELRO
5. QTV
6. Routemarks
7. Ilto Logistics

Rules for Picking a Company Name
1. Unique and unforgettable
2. Avoid unusual spellings
3. Easy to pronounce and remember
4. Keep it simple
5. Make some sense
6. Give a clue

Rules for Picking a Company Logo
4. Keep it simple
5. Make some sense
6. Give a clue

1. Simplicity
2. Memorability
3. Originality
4. Modern Yet Timeless
5. Balance
6. Complementary
7. Versatility

Stationery Information
1. Company Name : ZENFreight Solutions Sdn Bhd
2. Company Registration : 2837165-W
3. Address : 42-08, Jalan Cempaka Indah 5, Taman Seri Bayu, 81300 Johor Bahru, Johor, Malaysia.
4. Name : Derek Tan
5. Position : Manager
6. Mobile No : (+6019) 4381907
7. Office No : (+607) 5218764
8. Fax No : Not Available
9. Email Address : derek.tan@zenfreight-solutions.example
10. Web Domain : www.zenfreight-solutions.example
11. Company Slogan : Be Globally Connected

Target Market(s)

Corporate Company

Industry/Entity Type

Shipping and Logistics Industry

Requirements
Must have
• Company Full Name : ZENFREIGHT SOLUTIONS SDN. BHD.
Nice to have
• Keep it simple and unforgettable ...

```html
<!DOCTYPE html>
<html lang="en">
<head>
<meta charset="utf-8">
<title>ZENFreight Solutions – Business Card</title>
<link rel="stylesheet" href="https://fonts.googleapis.com/css2?family=Montserrat:wght@700&family=Open+Sans:wght@400;600&display=swap">
<style>
  :root {
    --brand-blue: #2e8bdb;
    --ink-dark: #262626;
    --paper: #ffffff;
    --backdrop: #2b2b2b;
    --divider: rgba(46, 139, 219, 0.55);
  }
  * { margin: 0; padding: 0; box-sizing: border-box; }
  html, body { width: 1200px; height: 1015px; overflow: hidden; }
  body {
    background: var(--backdrop);
    display: flex;
    flex-direction: column;
    align-items: center;
    justify-content: center;
    gap: 44px;
    font-family: "Open Sans", sans-serif;
  }
  .card {
    position: relative;
    width: 760px;
    height: 434px;
    overflow: hidden;
  }

  /* Front */
  .card-front { background: var(--brand-blue); color: var(--paper); }
  .card-front .registration {
    position: absolute; top: 44px; left: 70px;
    font-size: 14px; letter-spacing: 0.5px;
  }
  .brand {
    display: flex; align-items: center; gap: 26px;
  }
  .brand-square {
    width: 96px; height: 96px;
    border: 9px solid currentColor;
  }
  .brand-name {
    font-family: "Montserrat", sans-serif;
    font-weight: 700;
    line-height: 1;
  }
  .brand-name .main { display: block; font-size: 58px; letter-spacing: 3px; }
  .brand-name .sub { display: block; font-size: 21px; letter-spacing: 5px; margin-top: 10px; }
  .card-front .brand { position: absolute; top: 130px; left: 70px; }
  .card-front .slogan {
    position: absolute; left: 70px; bottom: 70px;
    font-family: "Montserrat", sans-serif; font-weight: 700;
    font-size: 22px; letter-spacing: 3px;
  }

  /* Back */
  .card-back { background: var(--paper); }
  .band-blue {
    position: absolute; left: 0; right: 0; top: 262px; height: 96px;
    background: var(--brand-blue);
  }
  .band-dark {
    position: absolute; left: 0; right: 0; top: 358px; bottom: 0;
    background: var(--ink-dark);
  }
  .card-back .brand { position: absolute; top: 44px; left: 110px; color: var(--ink-dark); }
  .card-back .brand-square { border-color: var(--brand-blue); }
  .holder {
    position: absolute; left: 70px; top: 280px;
    color: var(--paper); text-align: right; width: 250px;
  }
  .holder .name {
    font-family: "Montserrat", sans-serif; font-weight: 700;
    font-size: 34px; letter-spacing: 1px; line-height: 1.1;
  }
  .holder .role { font-size: 20px; }
  .divider {
    position: absolute; left: 345px; top: 190px; width: 2px; height: 150px;
    background: var(--divider);
  }
  .contacts {
    position: absolute; left: 370px; top: 178px;
    list-style: none; color: var(--brand-blue); font-size: 16px;
  }
  .contacts li { display: flex; align-items: center; gap: 8px; line-height: 1.65; }
  .contacts svg { width: 16px; height: 16px; flex: none; }
  .address {
    position: absolute; left: 0; right: 0; top: 368px;
    text-align: center; color: var(--paper); font-size: 17px; line-height: 1.45;
  }
</style>
</head>
<body>

  <section class="card card-front" aria-label="Card front">
    <p class="registration">Registration : 2837165-W</p>
    <div class="brand">
      <span class="brand-square" aria-hidden="true"></span>
      <p class="brand-name"><span class="main">ZENFREIGHT</span><span class="sub">SOLUTIONS SDN. BHD</span></p>
    </div>
    <p class="slogan">BE GLOBALLY CONNECTED</p>
  </section>

  <section class="card card-back" aria-label="Card back">
    <div class="band-blue"></div>
    <div class="band-dark"></div>

    <div class="brand">
      <span class="brand-square" aria-hidden="true"></span>
      <p class="brand-name"><span class="main">ZENFREIGHT</span><span class="sub">SOLUTIONS SDN. BHD</span></p>
    </div>

    <div class="holder">
      <p class="name">DEREK TAN</p>
      <p class="role">Manager</p>
    </div>

    <div class="divider"></div>

    <ul class="contacts">
      <li>
        <svg viewBox="0 0 24 24" fill="currentColor" aria-hidden="true"><path d="M6.6 10.8a15 15 0 0 0 6.6 6.6l2.2-2.2a1 1 0 0 1 1-.25 11.4 11.4 0 0 0 3.6.57 1 1 0 0 1 1 1V20a1 1 0 0 1-1 1A17 17 0 0 1 3 4a1 1 0 0 1 1-1h3.5a1 1 0 0 1 1 1c0 1.25.2 2.45.57 3.57a1 1 0 0 1-.25 1z"/></svg>
        (+6019) 4381907
        <svg viewBox="0 0 24 24" fill="none" stroke="currentColor" stroke-width="2" aria-hidden="true"><rect x="6" y="2" width="12" height="20" rx="2"/><line x1="11" y1="18" x2="13" y2="18"/></svg>
        (+607) 5218764
      </li>
      <li>
        <svg viewBox="0 0 24 24" fill="none" stroke="currentColor" stroke-width="2" aria-hidden="true"><rect x="2" y="5" width="20" height="14"/><path d="M2 5l10 8 10-8"/></svg>
        derek.tan@zenfreight-solutions.example
      </li>
      <li>
        <svg viewBox="0 0 24 24" fill="none" stroke="currentColor" stroke-width="2" aria-hidden="true"><circle cx="12" cy="12" r="10"/><ellipse cx="12" cy="12" rx="4" ry="10"/><line x1="2" y1="12" x2="22" y2="12"/></svg>
        www.zenfreight-solutions.example
      </li>
    </ul>

    <p class="address">42-08, Jalan Cempaka Indah 5, Taman Seri Bayu<br>81300 Johor Bahru, Johor, Malaysia</p>
  </section>

</body>
</html>
```